Stylish Business Cards Wanted

- DOUBLE SIDED Design Required -

High end, edgy cards for a corporate and personal stylist. Must include logo,
Name: Belinda Harwick
Title: Director and Stylist
telephone : +61 8 7142 5809
email: belinda@theloombriefing.example
website: theloombriefing.example
Tag: Corporate Workwear & Uniform Specialist | Personal Stylist
Would like nice icons for telephone, email, website

Target Market(s)

Businesses wanting stylish uniforms, people wanting stylish wardrobes

Industry/Entity Type

Corporate Workwear Stylist

Contact Information for Business Card

I would like black, white and gold foiling incorporated in the design - possibly a touch of the other colours on my branding guide attached Name: Belinda Harwick Title: Director and Stylist telephone : +61 8 7142 5809 email: belinda@theloombriefing.example website: theloombriefing.example Tag: Corporate Workwear & Uniform Specialist | Personal Stylist Would like nice icons for telephone, email, website

Font styles to use
Other font styles liked:
• Raleway

Colors

Designer to choose colors to be used in the design.

Requirements
Must have
• Gold foil accents

```html
<!DOCTYPE html>
<html lang="en">
<head>
<meta charset="utf-8">
<title>The Loom Briefing – Business Cards</title>
<link href="https://fonts.googleapis.com/css2?family=Roboto:wght@400;500&display=swap" rel="stylesheet">
<style>
  :root {
    --backdrop: #161616;
    --card: #232323;
    --gold: #e8b94a;
    --white: #ffffff;
  }
  * { margin: 0; padding: 0; box-sizing: border-box; }
  html, body {
    width: 1200px; height: 1059px; overflow: hidden;
    background: var(--backdrop);
    font-family: 'Roboto', Arial, sans-serif;
  }
  .canvas { position: relative; width: 1200px; height: 1059px; }
  .card {
    position: absolute;
    width: 690px; height: 392px;
    background: var(--card);
    border-radius: 18px;
  }
  .card--front { left: 256px; top: 89px; }
  .card--back { left: 255px; top: 548px; }

  .brand {
    position: absolute;
    color: var(--white);
    font-weight: 500;
    text-align: center;
    line-height: 1.1;
  }
  .card--front .brand {
    left: 92px; top: 150px; width: 220px;
    font-size: 30px;
  }
  .card--back .brand {
    left: 0; right: 0; top: 150px;
    font-size: 46px;
  }

  .identity { position: absolute; left: 362px; top: 127px; }
  .identity__name {
    color: var(--gold);
    font-weight: 500;
    font-size: 23px;
    letter-spacing: 0.2px;
    line-height: 1;
  }
  .identity__title {
    color: var(--white);
    font-size: 16.5px;
    margin-top: 6px;
  }
  .identity__rule {
    width: 276px; height: 1px;
    background: var(--gold);
    margin-top: 12px;
  }
  .contact { list-style: none; margin-top: 12px; }
  .contact__item {
    display: flex; align-items: center;
    color: var(--white);
    font-size: 16.5px;
    height: 24px;
  }
  .contact__icon { width: 15px; height: 15px; margin-right: 6px; flex: none; }

  .tagline {
    position: absolute;
    left: 102px; top: 343px;
    color: var(--white);
    font-size: 16.5px;
    white-space: nowrap;
  }
</style>
</head>
<body>
<main class="canvas">
  <section class="card card--front">
    <div class="brand">The Loom<br>Briefing</div>

    <div class="identity">
      <div class="identity__name">BELINDA HARWICK</div>
      <div class="identity__title">Director and Stylist</div>
      <div class="identity__rule"></div>
      <ul class="contact">
        <li class="contact__item">
          <svg class="contact__icon" viewBox="0 0 24 24" aria-hidden="true">
            <path fill="#e8b94a" d="M6.6 10.8a15.1 15.1 0 0 0 6.6 6.6l2.2-2.2a1 1 0 0 1 1-.25 11.4 11.4 0 0 0 3.6.57 1 1 0 0 1 1 1V20a1 1 0 0 1-1 1A17 17 0 0 1 3 4a1 1 0 0 1 1-1h3.5a1 1 0 0 1 1 1c0 1.25.2 2.45.57 3.57a1 1 0 0 1-.25 1z"/>
          </svg>
          +61 8 7142 5809
        </li>
        <li class="contact__item">
          <svg class="contact__icon" viewBox="0 0 24 24" aria-hidden="true">
            <rect x="2" y="5" width="20" height="14" fill="#e8b94a"/>
            <path d="M2 5l10 8 10-8M2 19l7.5-7M22 19l-7.5-7" stroke="#232323" stroke-width="1.6" fill="none"/>
          </svg>
          belinda@theloombriefing.example
        </li>
        <li class="contact__item">
          <svg class="contact__icon" viewBox="0 0 24 24" aria-hidden="true">
            <circle cx="12" cy="12" r="10" fill="#e8b94a"/>
            <path d="M2 12h20M12 2c3 3 3 17 0 20M12 2c-3 3-3 17 0 20" stroke="#232323" stroke-width="1.4" fill="none"/>
          </svg>
          www.theloombriefing.example
        </li>
      </ul>
    </div>

    <p class="tagline">Corporate Workwear &amp; Uniform Specialist | Personal Stylist</p>
  </section>

  <section class="card card--back">
    <div class="brand">The Loom Briefing</div>
  </section>
</main>
</body>
</html>
```